Business Card Design - Photographer

I am a landscape photographer and I require a business card design. 

I require two designs:
1)  a double sided business card
 and
b)  a single sided business card 

The single sided design can either be the same as the double sided (with just one side having all the information)....or it can be an entire new design. Its up to you.

My corporate colours are (CMYK):

Blue   69, 32, 0, 0
Grey  72,  64,  47,  31
Green  32,  2,  91,  0
Yellow   0, 19, 92, 0
Orange  0, 39, 75, 0

Colour space in final file should be in CMYK.

The details that need to be included on the card:

- Use the provided Logo
- Name: Wiktor Baranowski
- Email:   sales@vistalumeworks.com.au
- Website:    vistalumeworks.com.au
- Twitter:    twitter.com/vistalumeworks
- Facebook:   facebook.com/vistalumeworks
- Mobile  0417 539 662

Please use the attached template to design the logo to the specified size, including the marked bleed lines. I have also attached my logo in PNG (transparent background) and ai format for you to use.

The final file should be:
- Photoshop version with layers so I can edit the name/text etc. All non vector files should be high resolution at 1039 x 697 pixels at 300 dpi.

I also require a file as:
- Vector based PDF

Anyway questions please contact me.

Thank you

Industry/Entity Type

Landscape

Logo styles of interest
Pictorial/Combination Logo
Abstract Logo
Wordmark Logo
Lettermark Logo
Requirements
Must have
• The details that need to be included on the card:

- Use the provided Logo
- Name: Wiktor Baranowski
- Email: sales@vistalumeworks.com.au
- Website: vistalumeworks.com.au
- Twitter: twitter.com/vistalumeworks
- Facebook: facebook.com/vistalumeworks
- Mobile 0417 539 662

```html
<!DOCTYPE html>
<html lang="en">
<head>
<meta charset="utf-8">
<title>Vistalume Works – Business Cards</title>
<link rel="stylesheet" href="https://fonts.googleapis.com/css2?family=Source+Sans+3:wght@400;600&display=swap">
<style>
  :root {
    --stage: #a8852f;
    --card-white: #ffffff;
    --brand-grey: #3b3f4f;
    --panel-dark: #0d0f16;
    --panel-mid: #2c3140;
    --divider: #5a5f6e;
    --text-light: #f2f3f6;
    --brand-blue: #3a9ad9;
    --card-shadow: rgba(0, 0, 0, 0.45);
  }
  * { box-sizing: border-box; margin: 0; padding: 0; }
  html, body { width: 1200px; height: 686px; overflow: hidden; }
  body {
    position: relative;
    background: var(--stage);
    font-family: "Source Sans 3", "Helvetica Neue", Arial, sans-serif;
  }
  .card {
    position: absolute;
    width: 492px;
    height: 281px;
    border-radius: 18px;
    background: var(--card-white);
    overflow: hidden;
    box-shadow: 1px 2px 3px var(--card-shadow);
  }
  .card--info { left: 81px; top: 107px; }
  .card--brand { left: 620px; top: 309px; }

  .brand-lockup {
    position: absolute;
    display: flex;
    align-items: center;
    gap: 8px;
    color: var(--brand-grey);
    font-weight: 600;
    letter-spacing: 0.06em;
    text-transform: uppercase;
    white-space: nowrap;
  }
  .brand-lockup__dot {
    border-radius: 50%;
    background: var(--brand-grey);
    flex: none;
  }
  .card--info .brand-lockup {
    left: 129px; top: 164px;
    transform: translateX(-50%);
    font-size: 19px;
  }
  .card--info .brand-lockup__dot { width: 14px; height: 14px; }
  .card--brand .brand-lockup {
    left: 244px; top: 166px;
    transform: translateX(-50%);
    font-size: 28px;
  }
  .card--brand .brand-lockup__dot { width: 20px; height: 20px; }

  .divider {
    position: absolute;
    left: 274px; top: 0;
    width: 3px; height: 100%;
    background: var(--divider);
  }
  .contact-panel {
    position: absolute;
    left: 279px; top: 0; right: 0; bottom: 0;
    background: radial-gradient(circle at 30% 35%, var(--panel-mid) 0%, var(--panel-dark) 75%);
    color: var(--text-light);
  }
  .contact-list {
    position: absolute;
    left: 9px; top: 75px;
    list-style: none;
    font-size: 13px;
    line-height: 18px;
  }
  .contact-list li { display: flex; align-items: center; gap: 4px; }
  .contact-list svg { width: 11px; height: 11px; flex: none; }
  .social-list {
    position: absolute;
    left: 10px; top: 143px;
    list-style: none;
    font-size: 12px;
  }
  .social-list li { display: flex; align-items: center; gap: 4px; height: 23px; }
  .social-list__mark {
    width: 15px; height: 15px;
    border-radius: 2px;
    background: var(--brand-blue);
  }
  .address {
    position: absolute;
    left: 12px; top: 193px;
    font-size: 13px;
    line-height: 16px;
  }
</style>
</head>
<body>
  <section class="card card--info" aria-label="Business card, contact side">
    <div class="brand-lockup">
      <span class="brand-lockup__dot"></span>Vistalume Works
    </div>
    <div class="divider"></div>
    <div class="contact-panel">
      <ul class="contact-list">
        <li>
          <svg viewBox="0 0 12 12" aria-hidden="true"><path d="M2.5 1 L4.5 1 L5 3.5 L3.8 4.5 Q5 7 7.5 8.2 L8.5 7 L11 7.5 L11 9.5 Q10.5 11 9 11 Q1 10 1 3 Q1 1.5 2.5 1 Z" fill="currentColor"/></svg>
          0417 539 662
        </li>
        <li>
          <svg viewBox="0 0 12 12" aria-hidden="true"><rect x="0.5" y="2.5" width="11" height="7" fill="currentColor"/><path d="M0.5 2.5 L6 6.5 L11.5 2.5" stroke="#0d0f16" stroke-width="1" fill="none"/></svg>
          sales@vistalumeworks.com.au
        </li>
        <li>
          <svg viewBox="0 0 12 12" aria-hidden="true"><g fill="none" stroke="currentColor" stroke-width="1"><circle cx="6" cy="6" r="5"/><ellipse cx="6" cy="6" rx="2.2" ry="5"/><path d="M1 6 H11 M2 3.5 H10 M2 8.5 H10"/></g></svg>
          www.vistalumeworks.com.au
        </li>
      </ul>
      <ul class="social-list">
        <li><span class="social-list__mark"></span>@vistalumeworks</li>
        <li><span class="social-list__mark"></span>@vistalumeworks</li>
      </ul>
      <p class="address">Street name City<br>State, zip code</p>
    </div>
  </section>

  <section class="card card--brand" aria-label="Business card, brand side">
    <div class="brand-lockup">
      <span class="brand-lockup__dot"></span>Vistalume Works
    </div>
  </section>
</body>
</html>
```